Sleep/Snoring Business - Requires Website - Australia

We are seeking a simple to maintain website for our sleep business. The health care business provides diagnostic and treatment solutions for snoring, sleep disorders and other respiratory problems.

Ideally, colours to match the company logo (attached).

The page must be built using WORDPRESS.

Ideally site will have a home page outlining the business, with 5 sub pages - being "Diagnosis" "Treatment Options", "Prodcuts", "About Us", "Contact Us"

The site home page should include a large picture on the home page.

The "Treatment Options" and "Diagnosis" pages must include:
Allow for a few pictures with assocaited text, plus space for some embeded youtube videos.

"Prodcuts" page should have the ability to show 3-4 products across the page with text below.. that can include external URL to products

The "About Us" page must include:
1. a Map (google map) to identify the various locations. There are 6 in total.
2. A Section to describe our doctors/staff - allow for a picture and some text

The "Contact Us" page must include:
email form
telephone details

The overall design should have a clean and medical/safe feeling

Target Market(s)

People who snore and those with sleeping and respiratory disorders

Industry/Entity Type

Health Care

Coding

Coded - Design and coding required

Number of Pages Required

5+ page

Colors

Designer to choose colors to be used in the design.

Requirements
Must have
• The page must be built using WORDPRESS.
• Ideally site will have a home page outlining the business, with 5 sub pages - being "Diagnosis" "Treatment Options", "Prodcuts", "About Us", "Contact Us"
• The site home page should include a large picture on the home page.
• The "Treatment Options" and "Diagnosis" pages must include:
• Allow for a few pictures with assocaited text, plus space for some embeded youtube videos.
• "Prodcuts" page should have the ability to show 3-4 products across the page with text below.. that can include external URL to products
• The "About Us" page must include:
• 1. a Map (google map) to identify the various locations. There are 6 in total.
• 2. A Section to describe our doctors/staff - allow for a picture and some text
• The "Contact Us" page must include:
• email form
• telephone details
• Pictures must be licenced or free to use
Nice to have
• Home page pictures showing people sleeping well, snoring or fresh air (landscape) type transition pictures (at least 3).
Should not have
• Not to look cheap
• This is a high end healthcare business, so must look that way

```html
<!DOCTYPE html>
<html lang="en">
<head>
<meta charset="utf-8">
<title>About Us – Restwell</title>
<link rel="stylesheet" href="https://fonts.googleapis.com/css2?family=Roboto:wght@400;500&family=Roboto+Condensed:wght@700&display=swap">
<style>
:root{
  --navy:#0f3d73;
  --blue:#1d5791;
  --ink:#333;
  --line:#ddd;
  --footer:#f4f4f4;
}
*{margin:0;padding:0;box-sizing:border-box}
html,body{width:826px;height:1200px;overflow:hidden;background:#fff}
body{font-family:"Roboto",Arial,sans-serif;color:var(--ink);position:relative}
h1,h2,h3,h4{font-weight:400}
.abs{position:absolute}

/* header */
.brand{left:68px;top:24px;font-weight:500;font-size:34px;line-height:40px;color:var(--navy);letter-spacing:-1px;display:flex;align-items:center;gap:6px}
.brand-dot{width:11px;height:11px;border-radius:50%;background:var(--blue)}
.contact-bar{top:11px;font-size:10.5px;line-height:14px;color:#333;white-space:nowrap}
.contact-bar svg{position:absolute}
.contact-phone{left:453px}
.contact-phone svg{left:-26px;top:6px}
.contact-mail{left:615px}
.contact-mail svg{left:-38px;top:8px}
.contact-divider{position:absolute;left:-8px;top:4px;width:1px;height:22px;background:var(--line)}
.nav{top:57px;right:68px;display:flex;gap:22px;font-size:9.8px;text-transform:uppercase;color:#222}
.nav .active{color:var(--blue)}

/* hero */
.hero{left:0;top:83px;width:826px;height:190px}
.hero-title{top:164px;width:826px;text-align:center;font-family:"Roboto Condensed",Arial,sans-serif;font-weight:700;font-size:28px;color:#fff}

/* queries */
.queries{top:298px;width:826px;text-align:center;font-family:"Roboto Condensed",Arial,sans-serif;font-weight:700;font-size:24px;line-height:30px;color:var(--navy)}

/* locations */
.map{width:331px;height:179px;border:1px solid #ccc;padding:3px;background:#fff}
.map-fill{width:100%;height:100%;background:linear-gradient(135deg,#d6d3cb,#e3e1dc 55%,#d3d9cc)}
.map-fill.coast{background:linear-gradient(90deg,#b9cee4,#d8d8d4 60%,#dedcd6)}
.loc-title{font-family:"Roboto Condensed",Arial,sans-serif;font-weight:700;font-size:14.5px;color:var(--navy);text-transform:uppercase}
.loc-addr{font-size:9.8px;color:#333;display:flex;align-items:center;gap:6px;white-space:nowrap}
.loc-addr .sep{width:1px;height:11px;background:var(--line)}

/* footer */
.footer{left:0;top:962px;width:826px;height:198px;background:var(--footer);border-top:1px solid #eee}
.footer-brand{left:68px;top:1040px;font-weight:500;font-size:38px;color:var(--navy);letter-spacing:-1px}
.footer-head{font-size:12px;font-weight:400;color:#444;text-transform:uppercase;letter-spacing:.2px}
.footer-list{list-style:none;font-size:8.5px;color:#555}
.footer-contact li{position:relative;padding-left:16px;margin-bottom:8px;line-height:14px;width:160px}
.footer-contact svg{position:absolute;left:0;top:2px}
.footer-links li{margin-bottom:5px;padding-left:14px;position:relative;font-size:8px;line-height:9px}
.footer-links li::before{content:"›";position:absolute;left:2px;top:-1px;color:#666}
.copyright{top:1160px;width:826px;height:40px;border-top:1px solid #e5e5e5;text-align:center;font-size:7.5px;line-height:38px;color:#444}
</style>
</head>
<body>

<header>
  <div class="abs brand"><span>Restwell</span><span class="brand-dot"></span></div>

  <div class="abs contact-bar contact-phone">
    <svg width="12" height="14" viewBox="0 0 12 14"><path d="M3 1l2 3-1.5 1.5c.8 2 2 3.3 3.8 4.3L9 8.3l2.5 2L10 12.5C5 12 1.5 7 1.3 2.5z" fill="none" stroke="#555" stroke-width="1"/></svg>
    Phone - 08 5550 1427<br>Fax - 08 5550 1488
  </div>
  <div class="abs contact-bar contact-mail">
    <span class="contact-divider"></span>
    <svg width="16" height="12" viewBox="0 0 16 12"><rect x="1" y="1" width="14" height="10" rx="1" fill="none" stroke="#333" stroke-width="1.2"/><path d="M1 1l7 6 7-6" fill="none" stroke="#333" stroke-width="1.2"/></svg>
    Request an Appointment<br>bookings@restwellclinic.com.au
  </div>

  <nav class="abs nav">
    <span>Home</span><span>Diagnosis</span><span>Treatment Options</span><span class="active">About Us</span><span>Contact Us</span>
  </nav>
</header>

<svg class="abs hero" viewBox="0 0 826 190" role="img" aria-label="Calm bedroom photograph in blue tones behind the page title">
  <defs>
    <linearGradient id="heroTone" x1="0" y1="0" x2="1" y2="1">
      <stop offset="0" stop-color="#2a5e96"/><stop offset="1" stop-color="#1b4f86"/>
    </linearGradient>
    <radialGradient id="heroShadow" cx=".5" cy="0" r=".5">
      <stop offset="0" stop-color="#000" stop-opacity=".22"/><stop offset="1" stop-color="#000" stop-opacity="0"/>
    </radialGradient>
  </defs>
  <ellipse cx="413" cy="168" rx="330" ry="26" fill="url(#heroShadow)"/>
  <path d="M0 0H826V122Q413 210 0 122Z" fill="url(#heroTone)"/>
  <path d="M0 122Q413 210 826 122" fill="none" stroke="#8fb0d6" stroke-width="3"/>
</svg>
<h1 class="abs hero-title">ABOUT US</h1>

<h2 class="abs queries">FOR ALL QUERIES CONTACT<br>(08) 5550 1427</h2>

<section class="locations">
  <div class="abs map" style="left:68px;top:394px"><div class="map-fill" role="img" aria-label="Street map of the West Perth clinic location"></div></div>
  <div class="abs map" style="left:427px;top:394px"><div class="map-fill" role="img" aria-label="Street map of the Mandurah clinic location"></div></div>
  <h3 class="abs loc-title" style="left:68px;top:590px">West Perth</h3>
  <p class="abs loc-addr" style="left:68px;top:615px"><svg width="7" height="10" viewBox="0 0 7 10"><path d="M3.5 0a3.5 3.5 0 0 0-3.5 3.5C0 6 3.5 10 3.5 10S7 6 7 3.5A3.5 3.5 0 0 0 3.5 0z" fill="var(--navy)"/><circle cx="3.5" cy="3.5" r="1.3" fill="#fff"/></svg><span class="sep"></span>Head Office Address: Level 3, 18 Kestrel Lane, West Perth, 6005</p>
  <h3 class="abs loc-title" style="left:427px;top:590px">Mandurah</h3>
  <p class="abs loc-addr" style="left:427px;top:615px"><svg width="7" height="10" viewBox="0 0 7 10"><path d="M3.5 0a3.5 3.5 0 0 0-3.5 3.5C0 6 3.5 10 3.5 10S7 6 7 3.5A3.5 3.5 0 0 0 3.5 0z" fill="var(--navy)"/><circle cx="3.5" cy="3.5" r="1.3" fill="#fff"/></svg><span class="sep"></span>Coastview Shopping Centre 42 Shoreline Road, Falcon, 6210</p>

  <div class="abs map" style="left:68px;top:667px"><div class="map-fill" role="img" aria-label="Street map of the Bunbury clinic location"></div></div>
  <div class="abs map" style="left:427px;top:667px"><div class="map-fill coast" role="img" aria-label="Street map of the Port Hedland clinic location near the harbour"></div></div>
  <h3 class="abs loc-title" style="left:68px;top:863px">Bunbury</h3>
  <p class="abs loc-addr" style="left:68px;top:888px"><svg width="7" height="10" viewBox="0 0 7 10"><path d="M3.5 0a3.5 3.5 0 0 0-3.5 3.5C0 6 3.5 10 3.5 10S7 6 7 3.5A3.5 3.5 0 0 0 3.5 0z" fill="var(--navy)"/><circle cx="3.5" cy="3.5" r="1.3" fill="#fff"/></svg><span class="sep"></span>Southbay Medical Centre 9-11 Banksia St South Bunbury, 6230</p>
  <h3 class="abs loc-title" style="left:427px;top:863px">Port Hedland</h3>
  <p class="abs loc-addr" style="left:427px;top:888px"><svg width="7" height="10" viewBox="0 0 7 10"><path d="M3.5 0a3.5 3.5 0 0 0-3.5 3.5C0 6 3.5 10 3.5 10S7 6 7 3.5A3.5 3.5 0 0 0 3.5 0z" fill="var(--navy)"/><circle cx="3.5" cy="3.5" r="1.3" fill="#fff"/></svg><span class="sep"></span>Harbourside Medical Centre 5 Marlin St Port Hedland, 6721</p>
</section>

<footer>
  <div class="abs footer"></div>
  <div class="abs footer-brand">Restwell</div>

  <h4 class="abs footer-head" style="left:258px;top:1006px">Contacts Us</h4>
  <ul class="abs footer-list footer-contact" style="left:258px;top:1030px;width:180px">
    <li><svg width="8" height="11" viewBox="0 0 7 10"><path d="M3.5 0a3.5 3.5 0 0 0-3.5 3.5C0 6 3.5 10 3.5 10S7 6 7 3.5A3.5 3.5 0 0 0 3.5 0z" fill="none" stroke="#999"/><circle cx="3.5" cy="3.5" r="1.2" fill="#999"/></svg>Level 3, 18 Kestrel Lane, West Perth, 6005</li>
    <li><svg width="9" height="9" viewBox="0 0 12 14"><path d="M3 1l2 3-1.5 1.5c.8 2 2 3.3 3.8 4.3L9 8.3l2.5 2L10 12.5C5 12 1.5 7 1.3 2.5z" fill="#999"/></svg>Phone: 08 5550 1427</li>
    <li><svg width="9" height="9" viewBox="0 0 9 9"><rect x="1" y="3" width="7" height="5" fill="#999"/><rect x="2.5" y="0.5" width="4" height="3" fill="none" stroke="#999"/></svg>Fax: 08 5550 1488</li>
    <li style="width:200px"><svg width="9" height="7" viewBox="0 0 9 7"><rect width="9" height="7" fill="#aaa"/><path d="M0 0l4.5 4L9 0" fill="none" stroke="#fff"/></svg>Email: bookings@restwellclinic.com.au</li>
  </ul>

  <h4 class="abs footer-head" style="left:510px;top:1006px">Quick Links</h4>
  <ul class="abs footer-list footer-links" style="left:510px;top:1033px">
    <li>Home</li><li>About us</li><li>Diagnosis</li><li>Treatment Options</li><li>Contact</li>
  </ul>

  <p class="abs copyright">©2017 Restwell ., All Rights Reserved.</p>
</footer>

</body>
</html>
```